Brightmoor Essentials colloidal silver spray for pets.

We need a label for an 8-oz cobalt blue spray bottle. We are a small company just starting to share the benefits of colloidal silver. Our first offering will be the 8-oz spray bottle for pets. We would also like to update our logo. The finished project should be crisp and incorporate a dog on the label. I have attached the information we would like on the label and our logo, which can be changed to match your vision.
Updates

Hi, I would like to remind you that we are using a cobalt blue bottle with a black sprayer and would like an updated logo. Also, for the business cards, we don't want an animal on them, as we are planning future products for people. thank you

```html
<!DOCTYPE html>
<html lang="en">
<head>
<meta charset="utf-8">
<title>Brightmoor Essentials – Colloidal Silver Pet Spray Label</title>
<link href="https://fonts.googleapis.com/css2?family=Sancreek&family=Baloo+2:wght@600;700;800&display=swap" rel="stylesheet">
<style>
  :root {
    --page-bg: #e6e6e6;
    --label-top: #d6dbef;
    --label-mid: #9fb0dc;
    --label-bottom: #4b66b3;
    --brand-grey: #4a4d55;
    --title-green: #078a45;
    --pill-navy: #2e3192;
    --white: #ffffff;
    --flag-red: #d52b1e;
    --photo-light: #d9a066;
    --photo-dark: #9a5a26;
  }
  * { margin: 0; padding: 0; box-sizing: border-box; }
  html, body {
    width: 1200px; height: 1200px; overflow: hidden;
    background: radial-gradient(circle at 50% 45%, #f6f6f6 0%, var(--page-bg) 70%, #d4d4d4 100%);
    font-family: "Baloo 2", sans-serif;
  }
  .label {
    position: absolute; left: 330px; top: 35px;
    width: 540px; height: 1130px; overflow: hidden;
    background: linear-gradient(180deg, var(--label-top) 0%, var(--label-mid) 45%, var(--label-bottom) 100%);
    text-align: center; color: var(--white);
  }
  .brand-name {
    position: absolute; top: 52px; left: 0; right: 0;
    font-size: 26px; font-weight: 800; color: var(--brand-grey);
    letter-spacing: 0.5px;
  }
  .product-title {
    position: absolute; top: 140px; left: 0;
    width: 540px; height: 240px;
  }
  .product-title text {
    font-family: "Sancreek", serif;
    font-size: 128px;
    fill: var(--title-green);
    stroke: var(--white);
    stroke-width: 6px;
    paint-order: stroke fill;
    stroke-linejoin: round;
  }
  .pill {
    position: absolute; top: 382px; left: 52px; width: 432px; height: 96px;
    background: var(--pill-navy); border-radius: 22px;
    font-size: 34px; font-weight: 800; line-height: 40px; letter-spacing: 1px;
    display: flex; flex-direction: column; justify-content: center;
  }
  .specs {
    position: absolute; top: 492px; left: 0; right: 0;
    font-size: 24px; font-weight: 700; line-height: 27px;
  }
  .divider {
    position: absolute; top: 555px; left: 108px; width: 322px; height: 2px;
    background: var(--white);
  }
  .claims {
    position: absolute; top: 567px; left: 0; right: 0;
    font-size: 21px; font-weight: 700; line-height: 24px;
  }
  .pet-photo {
    position: absolute; top: 672px; left: 30px; width: 480px; height: 458px;
    background: radial-gradient(ellipse at 50% 55%, var(--photo-light) 0%, var(--photo-dark) 65%, rgba(154,90,38,0) 100%);
    border-radius: 45% 45% 0 0;
  }
  .origin {
    position: absolute; top: 1076px; left: 54px;
    display: flex; align-items: center; gap: 10px;
  }
  .origin-text {
    text-align: left; color: var(--flag-red);
    font-size: 15px; font-weight: 600; line-height: 15px;
    border-left: 2px solid var(--flag-red); padding-left: 6px;
  }
  .volume {
    position: absolute; top: 1084px; right: 48px;
    font-size: 22px; font-weight: 800;
  }
</style>
</head>
<body>
  <main class="label">
    <div class="brand-name">Brightmoor Essentials</div>
    <svg class="product-title" viewBox="0 0 540 240" role="heading" aria-level="1" aria-label="Colloidal Silver">
      <text x="270" y="114" text-anchor="middle" textLength="476" lengthAdjust="spacingAndGlyphs">COLLOIDAL</text>
      <text x="270" y="222" text-anchor="middle" textLength="312" lengthAdjust="spacingAndGlyphs">SILVER</text>
    </svg>
    <div class="pill"><span>NATURAL FIRST AID</span><span>FOR PETS</span></div>
    <p class="specs">10 PPM - No Preservaties<br>100% Pure - No Additives</p>
    <div class="divider"></div>
    <p class="claims">Anti microbial, Anti Fungal,<br>Anti Bacterial, Anti Viral<br>Treats burns, Bites, Cuts, Abrasions,<br>Hots Spots</p>
    <div class="pet-photo" role="img" aria-label="Photo of a smiling fluffy orange Pomeranian dog"></div>
    <div class="origin">
      <svg class="flag" width="72" height="38" viewBox="0 0 72 38" aria-hidden="true">
        <rect width="72" height="38" fill="var(--white)"/>
        <rect width="18" height="38" fill="var(--flag-red)"/>
        <rect x="54" width="18" height="38" fill="var(--flag-red)"/>
      </svg>
      <div class="origin-text">MADE IN<br>CANADA</div>
    </div>
    <div class="volume">8 oz / 250 ml</div>
  </main>
</body>
</html>
```